Logo and Flyer design Helix Summit Australia 2019

A logo and flyer design for a 3D Medical printing conference to be held in Melbourne Australia. The conference audience is aimed at people who have an interesting in 3D printing to benefit their work as well as printing for a hobby. Mostly professionals in the medical, bio-engineering, VET sciences fields who are 3D printing models for patients and simulation will attend this conference.

Target Market(s)

medical, bio-engineering, VET sciences fields who are 3D printing models for patients and simulation will attend this conference.

Industry/Entity Type

Medical And Science

Font styles to use
Sans Serif

Colors
3276b5
e34197
fbee3d
f68d4c
f04a50

Requirements
Must have
• Helix Summit logo
• Jaw
• Futuristic theme
• Helix Summit colours
Nice to have
• Unique design
Should not have
• Pictures from google images

```html
<!DOCTYPE html>
<html lang="en">
<head>
<meta charset="UTF-8">
<title>Helix Summit Australia 2019 — Flyer</title>
<link href="https://fonts.googleapis.com/css2?family=Michroma&family=Open+Sans:wght@700&display=swap" rel="stylesheet">
<style>
  :root {
    --page-bg: #2b2b2e;
    --navy-deep: #0f1a4a;
    --navy: #17246b;
    --royal: #1f3a9c;
    --violet: #7a5fc0;
    --band: #d9dadc;
    --band-edge: #b9bcc1;
    --ink-light: #f2f4f8;
    --title-steel: #dfe6f2;
    --brand-red: #b3213d;
    --ring: #1a1638;
    --jaw-gold: #d9a323;
    --jaw-bg: #eef1f0;
  }
  * { margin: 0; padding: 0; box-sizing: border-box; }
  html, body {
    width: 1200px; height: 900px; overflow: hidden;
    background: var(--page-bg);
  }
  .flyer {
    position: absolute; left: 300px; top: 20px;
    width: 600px; height: 860px; overflow: hidden;
    background:
      radial-gradient(ellipse 55% 22% at 62% 34%, rgba(122,95,192,.55), transparent 70%),
      radial-gradient(ellipse 70% 30% at 30% 30%, rgba(60,110,220,.45), transparent 70%),
      linear-gradient(180deg, var(--royal) 0%, var(--navy) 45%, var(--navy-deep) 100%);
  }
  .flyer::before {
    content: ""; position: absolute; inset: 0;
    background: repeating-linear-gradient(135deg, rgba(255,255,255,.03) 0 2px, transparent 2px 6px);
  }
  .title {
    position: absolute; top: 96px; left: 0; right: 0;
    text-align: center; font-family: "Michroma", sans-serif;
    color: var(--title-steel);
  }
  .title__name {
    display: block; font-size: 40px; letter-spacing: 2px; line-height: 1.2;
    text-shadow: 0 2px 3px rgba(0,0,0,.45);
  }
  .title__edition {
    display: block; margin-top: 8px; font-size: 30px; letter-spacing: 3px;
    color: var(--ink-light);
  }
  .band {
    position: absolute; top: 352px; left: 0; width: 100%; height: 88px;
    background: linear-gradient(90deg, #f1f2f3 0%, var(--band) 40%, var(--band-edge) 100%);
  }
  .feature {
    position: absolute; left: 198px; top: 288px; width: 198px; height: 198px;
    border-radius: 50%; border: 8px solid var(--ring);
    background: radial-gradient(ellipse 60% 40% at 50% 55%, var(--jaw-gold) 0 45%, var(--jaw-bg) 75%);
  }
  .details {
    position: absolute; top: 600px; left: 0; right: 0;
    text-align: center; font-family: "Michroma", sans-serif;
    color: var(--ink-light); font-size: 26px; letter-spacing: 2px; line-height: 1.45;
  }
  .footer {
    position: absolute; bottom: 0; left: 0; width: 100%; height: 63px;
    background: linear-gradient(90deg, #f3f3f4, var(--band) 60%, var(--band-edge));
    display: flex; align-items: center; justify-content: center; gap: 8px;
  }
  .footer__mark {
    width: 40px; height: 40px; border-radius: 50%; background: var(--navy);
  }
  .footer__name {
    font-family: "Open Sans", sans-serif; font-weight: 700;
    font-size: 17px; color: var(--brand-red);
  }
</style>
</head>
<body>
  <main class="flyer">
    <h1 class="title">
      <span class="title__name">HELIX SUMMIT</span>
      <span class="title__edition">AUSTRALIA 2019</span>
    </h1>
    <div class="band"></div>
    <div class="feature" role="img" aria-label="Photo of a 3D printed amber jawbone model on a white surface"></div>
    <p class="details">14-15-16 NOVEMBER<br>MELBOURNE</p>
    <footer class="footer">
      <span class="footer__mark"></span>
      <span class="footer__name">Helix Print Lab</span>
    </footer>
  </main>
</body>
</html>
```